Dietitian needs awesome business card

I need a contemporary design that's eye catching but professional.
My card is to given to doctors, specialists and patients alike.
I manage patients with chronic diseases
I have uploaded my logo and current business card, I would also like the other Certified Clinical Nutritionist logo incorporated into the design

Target Market(s)

Doctors, specialists and patients

Industry/Entity Type

Healthcare

Contact Information for Business Card

www.brightfieldnutrition.com.au
Ph: 0427 561 903
Fax: 6457 2183
email: marcus.k.diet@fernmail.com
Space on the back of the card with: Appointment date, Appointment time and appointment location

Font styles to use
Serif

Colors
fbee3e
876aae
ffc214

Requirements
Must have
• My Logo
• Certified Clinical Nutritionist Logo
• My 4 locations - Pinebrook Medical Centre, North Corrin Health, Hollis Medical, Ashcombe Doctors Surgery
Nice to have
• I like the colours in my current business card

```html
<!DOCTYPE html>
<html lang="en">
<head>
<meta charset="utf-8">
<title>Brightfield Nutrition – Business Card</title>
<link href="https://fonts.googleapis.com/css2?family=Arimo:wght@400;700&display=swap" rel="stylesheet">
<style>
  :root {
    --bg: #e4e5e8;
    --card: #ffffff;
    --navy: #1e2f9a;
    --blue: #1a73c8;
    --sky: #2aa3e0;
    --lime: #9ccc1f;
    --orange: #f47a20;
    --ink: #2b3a8f;
    --grey: #6d6f78;
    --rule: #b9bcc6;
  }
  * { box-sizing: border-box; margin: 0; padding: 0; }
  html, body { width: 1200px; height: 950px; overflow: hidden; }
  body {
    background: var(--bg);
    font-family: "Arimo", Arial, sans-serif;
    position: relative;
  }
  .card {
    position: absolute;
    width: 620px;
    height: 378px;
    background: var(--card);
    box-shadow: 0 6px 18px rgba(0,0,0,.18);
    overflow: hidden;
  }
  .card--back { left: 110px; top: 60px; }
  .card--front { left: 470px; top: 500px; }

  /* brand lockup */
  .brand { position: absolute; display: flex; align-items: center; gap: 12px; white-space: nowrap; }
  .brand__mark {
    width: 50px; height: 50px; border-radius: 50%;
    background: var(--blue);
    flex: none;
  }
  .brand__name {
    font-size: 34px; font-weight: 400; color: var(--navy);
    line-height: 1; letter-spacing: -.5px;
  }
  .card--back .brand { left: 28px; top: 122px; gap: 9px; }
  .card--back .brand__mark { width: 34px; height: 34px; }
  .card--back .brand__name { font-size: 21px; letter-spacing: -.3px; }

  /* back: appointment */
  .badge {
    position: absolute; right: 34px; top: 22px;
    width: 130px; height: 58px; background: var(--orange);
  }
  .write-line {
    position: absolute; height: 1px; background: var(--rule);
  }
  .field-label {
    position: absolute; font-size: 15px; color: var(--ink);
  }
  .ampm {
    position: absolute; font-size: 11px; color: var(--ink);
  }
  .locations {
    position: absolute; list-style: none;
    font-size: 14px; color: var(--grey); line-height: 21px;
  }
  .locations li { display: flex; align-items: center; gap: 8px; }
  .locations li::before {
    content: ""; width: 11px; height: 11px;
    border: 1.5px solid var(--ink); display: block;
  }

  /* front */
  .swoosh { position: absolute; inset: 0; }
  .person {
    position: absolute; right: 34px; top: 30px; text-align: right; color: #fff;
  }
  .person__name { font-size: 22px; font-weight: 700; }
  .person__role { font-size: 14px; font-weight: 700; margin-top: 4px; }
  .card--front .brand { left: 34px; top: 222px; }
  .contact {
    position: absolute; left: 250px; top: 278px; list-style: none;
    font-size: 15px; color: var(--grey); line-height: 22px;
  }
  .contact li { display: flex; align-items: center; gap: 9px; }
  .contact svg { width: 14px; height: 14px; fill: var(--navy); flex: none; }
</style>
</head>
<body>

<section class="card card--back" aria-label="Appointment card">
  <div class="badge" role="img" aria-label="Certified Clinical Nutritionist badge"></div>

  <div class="write-line" style="left:300px; right:34px; top:100px;"></div>
  <div class="write-line" style="left:300px; right:34px; top:132px;"></div>
  <div class="write-line" style="left:300px; right:34px; top:164px;"></div>
  <div class="write-line" style="left:28px; right:34px; top:196px;"></div>

  <div class="brand">
    <span class="brand__mark"></span>
    <span class="brand__name">Brightfield Nutrition</span>
  </div>

  <span class="field-label" style="left:28px; top:232px;">Date :</span>
  <div class="write-line" style="left:78px; width:230px; top:250px;"></div>
  <ul class="locations" style="left:28px; top:262px;">
    <li>Pinebrook Medical Centre</li>
    <li>North Corrin Health</li>
  </ul>

  <span class="field-label" style="left:330px; top:232px;">Time :</span>
  <div class="write-line" style="left:382px; right:34px; top:250px;"></div>
  <span class="ampm" style="right:34px; top:234px;">AM/PM</span>
  <ul class="locations" style="left:330px; top:262px;">
    <li>Ashcombe Doctors Surgery</li>
    <li>Hollis Medical</li>
  </ul>
</section>

<section class="card card--front" aria-label="Business card front">
  <svg class="swoosh" viewBox="0 0 620 378" preserveAspectRatio="none" aria-hidden="true">
    <defs>
      <linearGradient id="band" x1="0" y1="0" x2="1" y2="0.3">
        <stop offset="0" stop-color="#1e2f9a"/>
        <stop offset="0.55" stop-color="#1a73c8"/>
        <stop offset="1" stop-color="#2a3fb0"/>
      </linearGradient>
    </defs>
    <path d="M0,0 H620 V70 C540,78 470,110 390,150 C300,196 200,212 110,196 C60,188 25,186 0,192 Z" fill="url(#band)"/>
    <path d="M0,192 C25,186 60,188 110,196 C200,212 300,196 390,150 C470,110 540,78 620,70 V80 C540,90 475,124 395,164 C300,212 200,226 110,210 C60,202 25,202 0,208 Z" fill="#9ccc1f"/>
  </svg>

  <div class="person">
    <div class="person__name">Marcus Kellaway</div>
    <div class="person__role">Nutritionist &amp; Chef</div>
  </div>

  <div class="brand">
    <span class="brand__mark"></span>
    <span class="brand__name">Brightfield Nutrition</span>
  </div>

  <ul class="contact">
    <li><svg viewBox="0 0 16 16"><path d="M3 1h3l1.5 4-2 1.3a9 9 0 0 0 4.2 4.2L11 8.5l4 1.5v3c0 1-1 2-2 2A13 13 0 0 1 1 3c0-1 1-2 2-2z"/></svg>0427 561 903</li>
    <li><svg viewBox="0 0 16 16"><path d="M4 1h8v4H4zM1 6h14v7h-3v2H4v-2H1zM5 10v4h6v-4z"/></svg>6457 2183</li>
    <li><svg viewBox="0 0 16 16"><path d="M1 3h14v10H1zM2 4l6 5 6-5v1L8 10 2 5z" fill-rule="evenodd"/></svg>marcus.k.diet@fernmail.com</li>
    <li><svg viewBox="0 0 16 16"><circle cx="8" cy="8" r="7"/><path d="M1 8h14M8 1c3 3 3 11 0 14M8 1c-3 3-3 11 0 14" stroke="#fff" stroke-width="1" fill="none"/></svg>www.brightfieldnutrition.com.au</li>
  </ul>
</section>

</body>
</html>
```